Velmor Spire Nine Flash website

we need a website to cater to 2 aspect of the business. We have Velmor spire residence and velmor spire office. For the office, we will get their inquire and arrange a face to face meetup to show them the office area for rent. For the residence side, it will need to be like staylane or roomvio.com. we want to allow them to book online for the date they need. We have a total of 10 different room configurations starting at $70 per night and up depending on the size of the room. example of the design is https://brisquelodge.com/

Target Market(s)

the website should have detail information on the layout, designs, and luxury of the building.

Industry/Entity Type

office and service appartment rental/lease

Coding

Coded - Design and coding required

Number of Pages Required

5+ page

Requirements
Must have
• a luxury perspective
Nice to have
• example https://brisquelodge.com/

```html
<!DOCTYPE html>
<html lang="en">
<head>
<meta charset="UTF-8">
<title>Velmor Spire Nine — Mobile Screens</title>
<link href="https://fonts.googleapis.com/css2?family=Montserrat:ital,wght@0,400;0,500;0,600;0,700;1,400;1,500;1,600;1,700&display=swap" rel="stylesheet">
<style>
  :root {
    --gold: #d19a2b;
    --gold-soft: #e7c27a;
    --gold-pale: #f1dfb8;
    --ink: #1e1e1e;
    --muted: #4a4a4a;
    --white: #ffffff;
    --navy: #1a3550;
  }
  * { margin: 0; padding: 0; box-sizing: border-box; }
  html, body { width: 1200px; height: 1200px; overflow: hidden; }
  body {
    background: var(--gold);
    font-family: "Montserrat", Arial, sans-serif;
    position: relative;
  }
  .screen {
    position: absolute;
    width: 356px;
    background: var(--white);
    overflow: hidden;
  }
  .screen--home { left: 38px; top: 140px; height: 1060px; border-radius: 8px 8px 0 0; }
  .screen--about { left: 414px; top: 0; height: 1200px; }
  .screen--rooms { left: 790px; top: 0; height: 1200px; }

  /* Home hero */
  .hero {
    position: absolute; left: 0; top: 0; width: 356px; height: 951px;
    background: linear-gradient(180deg, #1b3a58 0%, #1f3b55 30%, #3a4550 55%, #5a564e 75%, #2c2f33 100%);
  }
  .brand {
    position: absolute; left: 9px; top: 150px; width: 150px;
    color: var(--gold); font-size: 13px; font-weight: 500; letter-spacing: 0.5px;
    display: flex; align-items: center; gap: 6px; top: 40px; flex-direction: column;
  }
  .brand-mark { width: 34px; height: 34px; border: 1.5px solid var(--gold); }
  .menu-icon { position: absolute; left: 313px; top: 45px; }
  .hero-rule { position: absolute; left: 9px; top: 144px; width: 2px; height: 109px; background: var(--gold); }
  .hero-title {
    position: absolute; left: 10px; top: 268px;
    color: var(--white); font-size: 60px; font-weight: 600; font-style: italic;
    line-height: 74px; letter-spacing: -0.5px;
  }
  .hero-text {
    position: absolute; left: 9px; top: 536px; width: 336px;
    color: var(--white); font-size: 13px; font-style: italic; line-height: 22.7px;
  }
  .btn-contact {
    position: absolute; left: 10px; top: 822px; width: 335px; height: 49px;
    background: var(--gold); color: var(--white); font-size: 13px;
    display: flex; align-items: center; justify-content: center;
  }
  .welcome-rule { position: absolute; left: 10px; top: 1001px; width: 2px; height: 60px; background: var(--gold); }
  .welcome-title {
    position: absolute; left: 38px; top: 1012px;
    font-size: 34px; font-weight: 700; font-style: italic; color: var(--ink); line-height: 44px;
  }

  /* About screen */
  .feature-title {
    position: absolute; left: 10px;
    font-size: 35px; font-weight: 600; font-style: italic; color: var(--ink); line-height: 47px;
  }
  .feature-rule { position: absolute; left: 10px; width: 336px; height: 2px; background: var(--gold-soft); }
  .feature-text {
    position: absolute; left: 10px; width: 336px;
    font-size: 15px; font-style: italic; color: var(--muted); line-height: 25.5px;
  }
  .photo { position: absolute; left: 10px; width: 336px; }

  /* Rooms screen */
  .rooms-title {
    position: absolute; left: 0; top: 16px; width: 356px; text-align: center;
    font-size: 36px; font-weight: 600; font-style: italic; color: var(--ink); line-height: 46px;
  }
  .rooms-text {
    position: absolute; left: 8px; top: 143px; width: 340px; text-align: center;
    font-size: 15px; color: var(--muted); line-height: 25.6px;
  }
  .rooms-text strong { color: var(--ink); font-weight: 700; }
  .room-name {
    position: absolute; left: 0; top: 866px; width: 356px; text-align: center;
    font-size: 22px; font-weight: 600; font-style: italic; color: var(--ink);
  }
  .room-desc {
    position: absolute; left: 20px; top: 911px; width: 316px; text-align: center;
    font-size: 13.5px; color: var(--muted); line-height: 19.5px;
  }
</style>
</head>
<body>

  <section class="screen screen--home">
    <div class="hero" role="img" aria-label="Photo looking up at a high-rise residential tower against a deep blue sky"></div>
    <div class="brand"><span class="brand-mark"></span>Velmor Spire Nine</div>
    <svg class="menu-icon" width="25" height="18" viewBox="0 0 25 18" aria-label="Menu">
      <g stroke="#d19a2b" stroke-width="2"><line x1="0" y1="1" x2="25" y2="1"/><line x1="0" y1="9" x2="25" y2="9"/><line x1="0" y1="17" x2="25" y2="17"/></g>
    </svg>
    <div class="hero-rule"></div>
    <h1 class="hero-title">Privileges<br>and<br>Comfort</h1>
    <p class="hero-text">a place where warmth and luxury come together. Explore a blissful living or working experience in this special location. With the best facilities and stunning views, Velmor Spire invites you to experience the coolness of an elegant and inspiring lifestyle. Come discover magic in every corner, and experience the perfect balance of modern comfort and traditional charm, only at Velmor Spire.</p>
    <div class="btn-contact">Contact Us</div>
    <div class="welcome-rule"></div>
    <h2 class="welcome-title">Welcome to<br>Velmor Spire</h2>
  </section>

  <section class="screen screen--about">
    <h2 class="feature-title" style="top:8px">Irreplaceable<br>Experience</h2>
    <div class="feature-rule" style="top:108px"></div>
    <p class="feature-text" style="top:141px">We are committed to providing an unforgettable stay that exceeds your expectations and leaves lasting memories.</p>
    <div class="photo" style="top:270px;height:276px;background:linear-gradient(135deg,#3d4248 0%,#8a8d92 45%,#c9c8c6 70%,#5b4a45 100%)" role="img" aria-label="Photo of a guest relaxing with a cup in an armchair beside a lamp and window"></div>
    <h2 class="feature-title" style="top:605px">Best quality</h2>
    <div class="feature-rule" style="top:661px"></div>
    <p class="feature-text" style="top:694px">We only provide the best facilities that meet standards of excellence.</p>
    <div class="photo" style="top:772px;height:275px;background:linear-gradient(160deg,#8f8782 0%,#b3a8a2 45%,#c9b8b0 70%,#6d625c 100%)" role="img" aria-label="Photo of a freestanding stone bathtub beside a potted palm"></div>
    <h2 class="feature-title" style="top:1105px">Ultimate Luxury</h2>
    <div class="feature-rule" style="top:1161px;background:var(--gold-pale)"></div>
  </section>

  <section class="screen screen--rooms">
    <h2 class="rooms-title">Find Your Dream<br>Room</h2>
    <p class="rooms-text">Enjoy an unforgettable stay at Velmor Spire with the variety of room choices we offer. From cozy rooms for solo travelers to luxurious suites for large families, each of our rooms is designed with attention to detail and your comfort. <strong>Prices Start From $70 per Night</strong></p>
    <div class="photo" style="top:410px;height:440px;background:linear-gradient(180deg,#a9abad 0%,#d6d7d8 40%,#e9e9e9 70%,#3a3a3a 100%)" role="img" aria-label="Photo of a standard bedroom with a large window overlooking the city skyline"></div>
    <h3 class="room-name">Standard Room</h3>
    <p class="room-desc">A comfortable, classy space with all the facilities you need for a pleasant stay.</p>
    <div class="photo" style="top:970px;height:230px;background:linear-gradient(180deg,#5e5a52 0%,#8a8478 50%,#4a463f 100%)" role="img" aria-label="Photo of a warmly lit suite interior with framed art"></div>
  </section>

</body>
</html>
```